Stylish new business card needed!

Hello everyone! I am in need of a new business card design for an alarm company here in Hurricane WV. I have all fonts, color codes and logos provided for you use! We are a young company and like the style of a clean sleek looking business card. Would like it double sided, one side holding the logo and the other with your design!
Target Market(s)
The people that are looking for the newest tech for home automation and security
Industry/Entity Type
Alarm services; Home automation
Contact Information for Business Card
Name of person; position (Sales; Installer); Phone Number (555.418.7260); Employee cell Number; Website (www.GuardedByVelk.example); Employee Email; Double sided
Look and feel
Each slider illustrates characteristics of the customer's brand and the style your logo design should communicate.

```html
<!DOCTYPE html>
<html lang="en">
<head>
<meta charset="utf-8">
<title>Velk Business Card</title>
<link href="https://fonts.googleapis.com/css2?family=Arimo:wght@400;700&display=swap" rel="stylesheet">
<style>
  :root {
    --stage: #2a2a2c;
    --card-dark: #1e1e21;
    --brand-orange: #f0843f;
    --name-grey: #9a9a9c;
    --text-light: #f2f2f2;
    --divider: #8c8c8e;
  }
  * { box-sizing: border-box; margin: 0; padding: 0; }
  html, body {
    width: 1200px; height: 780px; overflow: hidden;
    background: var(--stage);
    font-family: "Arimo", Arial, sans-serif;
  }
  .canvas {
    position: relative; width: 1200px; height: 780px;
    display: flex; align-items: center; justify-content: center; gap: 60px;
  }
  .card {
    position: relative; width: 520px; height: 297px;
    border-radius: 4px; overflow: hidden;
    box-shadow: 0 10px 24px rgba(0,0,0,.45);
  }
  .card-front { background: var(--card-dark); }
  .holder { position: absolute; left: 46px; top: 52px; }
  .holder-name { font-size: 30px; font-weight: 700; letter-spacing: .3px; }
  .holder-first { color: var(--brand-orange); }
  .holder-last { color: var(--name-grey); }
  .holder-role { margin-top: 6px; margin-left: 60px; color: var(--text-light); font-size: 16px; }
  .divider { position: absolute; left: 200px; top: 120px; }
  .contact-list {
    position: absolute; left: 252px; top: 150px; list-style: none;
    color: var(--text-light); font-size: 16px; line-height: 25px;
  }
  .contact-item { display: flex; align-items: center; gap: 10px; }
  .contact-icon { width: 15px; height: 15px; flex: none; }
  .card-back { background: var(--brand-orange); }
  .pattern-field { position: absolute; inset: 0; background: linear-gradient(135deg, #f08d4c, #e87a35); }
  .brand-lockup {
    position: absolute; right: 40px; bottom: 38px;
    display: flex; align-items: center; gap: 8px;
  }
  .brand-name { color: #ffffff; font-size: 30px; font-weight: 700; }
  .brand-dot { width: 12px; height: 12px; border-radius: 50%; background: #ffffff; }
</style>
</head>
<body>
<main class="canvas">
  <section class="card card-front">
    <div class="holder">
      <p class="holder-name"><span class="holder-first">Mara</span> <span class="holder-last">Dovenko</span></p>
      <p class="holder-role">Sales; Installer</p>
    </div>
    <svg class="divider" width="60" height="110" viewBox="0 0 60 110">
      <line x1="58" y1="2" x2="2" y2="108" stroke="var(--divider)" stroke-width="1"/>
    </svg>
    <ul class="contact-list">
      <li class="contact-item">
        <svg class="contact-icon" viewBox="0 0 16 16"><path d="M4 1l3 3-2 2c1 2 3 4 5 5l2-2 3 3-2 3C7 15 1 9 1 3z" fill="var(--brand-orange)"/></svg>
        555.418.7260
      </li>
      <li class="contact-item">
        <svg class="contact-icon" viewBox="0 0 16 16"><rect x="4" y="1" width="8" height="14" rx="1.5" fill="none" stroke="var(--brand-orange)" stroke-width="1.5"/></svg>
        555.902.3318
      </li>
      <li class="contact-item">
        <svg class="contact-icon" viewBox="0 0 16 16"><circle cx="8" cy="8" r="6.5" fill="none" stroke="var(--brand-orange)" stroke-width="1.5"/><ellipse cx="8" cy="8" rx="3" ry="6.5" fill="none" stroke="var(--brand-orange)" stroke-width="1.2"/><line x1="1.5" y1="8" x2="14.5" y2="8" stroke="var(--brand-orange)" stroke-width="1.2"/></svg>
        www.GuardedByVelk.example
      </li>
      <li class="contact-item">
        <svg class="contact-icon" viewBox="0 0 16 16"><rect x="1" y="3" width="14" height="10" rx="1" fill="var(--brand-orange)"/><path d="M1.5 3.5L8 9l6.5-5.5" fill="none" stroke="var(--card-dark)" stroke-width="1.3"/></svg>
        info@GuardedByVelk.example
      </li>
    </ul>
  </section>

  <section class="card card-back">
    <div class="pattern-field" role="img" aria-label="Repeating brand name pattern in darker and lighter orange"></div>
    <div class="brand-lockup">
      <span class="brand-dot"></span>
      <span class="brand-name">Velk</span>
    </div>
  </section>
</main>
</body>
</html>
```